business card

Business card for new business.
Red and black corporate colors.
Card can have an Indsutrial feel to it. Feel free to add Rust, Bolted steel, or graphics as you see fit. We provide highly specialized services to the below mentioned industries.
Keep information out of corners so that if I want I can choose rounded corners.
Information
- front. name - title - phone - email
- Rear
Refining - Rail - Infrastructure - Mining - Energy
Calgary - Edmonton - Fort McMurray - Revelstoke - Vancouver

```html
<!DOCTYPE html>
<html lang="en">
<head>
<meta charset="utf-8">
<title>Ironvale – Business Card</title>
<link rel="stylesheet" href="https://fonts.googleapis.com/css2?family=Roboto:wght@400;700;900&display=swap">
<style>
  :root {
    --backdrop: #5b4738;
    --card-white: #f2f2f2;
    --brand-red: #e30016;
    --ink-grey: #555555;
    --mark-grey: #7a7a7a;
    --white: #ffffff;
    --black: #000000;
  }
  * { margin: 0; padding: 0; box-sizing: border-box; }
  html, body {
    width: 1200px; height: 960px; overflow: hidden;
    background: var(--backdrop);
    font-family: "Roboto", Arial, sans-serif;
  }
  .stage { position: relative; width: 1200px; height: 960px; }

  .card {
    position: absolute;
    width: 600px; height: 343px;
    box-shadow: 1px 2px 3px rgba(0,0,0,0.45);
  }
  .card--front { left: 314px; top: 113px; background: var(--card-white); }
  .card--back  { left: 312px; top: 472px; background: var(--brand-red); }

  .contact {
    position: absolute; left: 40px; top: 38px;
    font-size: 14px; line-height: 19px; color: var(--ink-grey);
    list-style: none;
  }
  .contact__web { color: var(--brand-red); }

  .brand-name {
    position: absolute; left: 44px; top: 236px;
    width: 230px; height: 56px;
    display: flex; align-items: center; justify-content: center;
    font-weight: 900; font-size: 40px; letter-spacing: 0.5px;
    color: var(--mark-grey);
  }

  .title-band {
    position: absolute; left: 278px; right: 0; top: 236px; height: 55px;
    background: var(--brand-red);
    color: var(--white);
    text-align: right; padding-right: 48px; padding-top: 7px;
  }
  .title-band__name { font-weight: 700; font-size: 22px; line-height: 24px; }
  .title-band__role { font-size: 15px; line-height: 18px; }

  .back-name {
    position: absolute; left: 0; right: 0; top: 118px;
    text-align: center;
    font-weight: 900; font-size: 44px; letter-spacing: 1px;
    color: var(--white);
  }

  .services {
    position: absolute; left: 0; right: 0; top: 256px;
    text-align: center; font-size: 14.5px; line-height: 18px;
  }
  .services__line {
    display: block; width: fit-content; margin: 0 auto;
    background: linear-gradient(90deg, var(--white) 0%, var(--white) 40%, #777 62%, var(--black) 78%);
    -webkit-background-clip: text; background-clip: text;
    color: transparent;
  }
</style>
</head>
<body>
<main class="stage">
  <section class="card card--front" aria-label="Card front">
    <ul class="contact">
      <li>604 555 0193</li>
      <li>info@ironvale.com</li>
      <li class="contact__web">www.ironvale.com</li>
    </ul>
    <div class="brand-name">IRONVALE</div>
    <div class="title-band">
      <div class="title-band__name">OWEN HARLOW</div>
      <div class="title-band__role">CEO/FOUNDER</div>
    </div>
  </section>

  <section class="card card--back" aria-label="Card back">
    <div class="back-name">IRONVALE</div>
    <p class="services">
      <span class="services__line">Refining • Rail • Infrastructure • Mining</span>
      <span class="services__line">Energy • Calgary • Edmonton • Fort McMurray</span>
      <span class="services__line">Revelstoke • Vancouver</span>
    </p>
  </section>
</main>
</body>
</html>
```